tinyTally Resource Book - 10 maths tasks to do outside

I need a 22 (11 pages back to back) page A6 sized book produced to standard for submission to professional printer. Needs to be as .pdf file showing guide lines and allowances for colour bleed. I have text already written and submitted as attachment in a Word file with margins set to A6 size. The theme of the materials is "Nature Play" so using lots of pictures from nature (Australia preferably) and showing lots of patterns in nature (rocks, leaves, flower petals etc). Some of the tasks refer to specific activities, such as "shadows" and "floating" so would be great to illustrate appropriately. The big emphasis is on learning outside the classroom, getting kids to engage actively with nature. I would like to see the pages as full colour - so not white background. The book itself will be spiral bound along the top edge so a margin of at least 1cm will be required at the top of each page (or the bottom of even numbered pages). Book will be printed on plastic laminated matte paper for outdoor use. Font size needs to be big enough to read. Fonts sizes, alignments and page numbers are all different at the moment and need to be standardised. One photo is included in a page as a sample if you can use it, otherwise disregard. Logo for Wattlebrook Numeracy Guild is also included to have as part of the acknowledgements at the back of the book.

Target Market(s)

Book is for early childhood and preschool teachers.

Industry/Entity Type

Education

Font styles to use
Sans Serif

Requirements
Must have
• Colour and appeal.
Nice to have
• Use of natural colours instead of bright catchy colours but that is your call.
Should not have
• American spelling

```html
<!DOCTYPE html>
<html lang="en-AU">
<head>
<meta charset="utf-8">
<title>tinyTally – 1. How Many Leaves?</title>
<link rel="stylesheet" href="https://fonts.googleapis.com/css2?family=Lilita+One&family=Didact+Gothic&display=swap">
<style>
  :root {
    --paper: #ffffff;
    --crop: #1a1a1a;
    --heading-green: #3f9a36;
    --heading-edge: #ffffff;
    --bullet-red: #d9232d;
    --body-ink: #3b3232;
    --leaf-yellow: #e9e3a6;
    --leaf-green: #b8cf9a;
    --leaf-rose: #d9a6a4;
    --leaf-plum: #a7868c;
    --leaf-moss: #9fb08a;
  }
  * { margin: 0; padding: 0; box-sizing: border-box; }
  html, body { width: 906px; height: 1200px; overflow: hidden; background: var(--paper); }
  .sheet { position: relative; width: 906px; height: 1200px; }

  .crop-marks { position: absolute; inset: 0; }

  .page-bleed {
    position: absolute; left: 54px; top: 54px; width: 797px; height: 1094px;
    background:
      linear-gradient(160deg, rgba(233,227,166,.85) 0%, rgba(217,166,164,.55) 22%, rgba(184,207,154,.7) 40%, rgba(167,134,140,.6) 58%, rgba(233,227,166,.7) 75%, rgba(159,176,138,.75) 100%),
      var(--leaf-green);
  }

  .task-content { position: absolute; left: 0; top: 0; width: 906px; height: 1200px; }

  .task-title, .section-heading {
    position: absolute; left: 127px;
    font-family: "Lilita One", "Arial Rounded MT Bold", sans-serif;
    color: var(--heading-green);
    text-shadow:
      2px 0 0 var(--heading-edge), -2px 0 0 var(--heading-edge),
      0 2px 0 var(--heading-edge), 0 -2px 0 var(--heading-edge),
      2px 2px 0 var(--heading-edge), -2px -2px 0 var(--heading-edge),
      2px -2px 0 var(--heading-edge), -2px 2px 0 var(--heading-edge);
    letter-spacing: .5px;
    line-height: 1;
  }
  .task-title { top: 146px; font-size: 48px; }
  .section-heading { font-size: 39px; }

  .point-list {
    position: absolute; left: 190px; list-style: none;
    font-family: "Didact Gothic", "Century Gothic", sans-serif;
    font-size: 30px; line-height: 42px; color: var(--body-ink);
    width: 620px;
  }
  .point-list li { position: relative; padding-left: 31px; }
  .point-list li::before {
    content: ""; position: absolute; left: 3px; top: 14px;
    width: 15px; height: 15px; background: var(--bullet-red);
    transform: rotate(45deg);
  }

  .heading-prompts { top: 440px; }
  .heading-variations { top: 648px; }
  .heading-big-ideas { top: 857px; }

  .list-steps { top: 200px; }
  .list-prompts { top: 492px; }
  .list-variations { top: 696px; }
  .list-big-ideas { top: 907px; }
</style>
</head>
<body>
<div class="sheet">
  <div class="page-bleed" role="img" aria-label="Background photograph of scattered autumn leaves in soft yellow, green, rose and plum tones"></div>

  <svg class="crop-marks" width="906" height="1200" viewBox="0 0 906 1200" aria-hidden="true">
    <g stroke="var(--crop)" stroke-width="1.2">
      <line x1="75" y1="0" x2="75" y2="38"/>
      <line x1="831" y1="0" x2="831" y2="38"/>
      <line x1="75" y1="1162" x2="75" y2="1200"/>
      <line x1="831" y1="1162" x2="831" y2="1200"/>
      <line x1="0" y1="75" x2="38" y2="75"/>
      <line x1="0" y1="1128" x2="38" y2="1128"/>
      <line x1="868" y1="75" x2="906" y2="75"/>
      <line x1="868" y1="1128" x2="906" y2="1128"/>
    </g>
  </svg>

  <main class="task-content">
    <h1 class="task-title">1. How Many Leaves?</h1>
    <ul class="point-list list-steps">
      <li>Get a collection of leaves</li>
      <li>Draw a 20cm x 20cm square (approx.) on the ground</li>
      <li>Find how many of the leaves it takes to cover the square</li>
    </ul>

    <h2 class="section-heading heading-prompts">Prompting questions</h2>
    <ul class="point-list list-prompts">
      <li>Will it be the same if I change the way I arrange the leaves? Try several different arrangements.</li>
    </ul>

    <h2 class="section-heading heading-variations">Variations</h2>
    <ul class="point-list list-variations">
      <li>Change the types of leaves used</li>
      <li>Change the size of the box</li>
      <li>Use bodies to measure big spaces</li>
    </ul>

    <h2 class="section-heading heading-big-ideas">Big Ideas</h2>
    <ul class="point-list list-big-ideas">
      <li>Area</li>
      <li>Measure</li>
      <li>Count</li>
      <li>Space</li>
    </ul>
  </main>
</div>
</body>
</html>
```